Harbor Crestline (Business Card Design)

Need business cards designed. Something modern, chic, and sleek. Mabye the back of the card should be the navy blue that is in the logo and then just the logo on the back.

Target Market(s)

Those in the hotel, office, and renovation industry

Contact Information for Business Card

1. Logo 2. Dorian Fenwick 3. CEO/Founder 4. Phone: (833) HarbCre / (833) 427-2731 5. Email: dorian@theharborcrestline.com 6. Website: www.theharborcrestline.com

Font styles to use
Other font styles liked:
• Look at the logo font and base the font for everything else off of that.

Colors
0054AA
0677BA
7BADD7
CADEEF
E8F1F8

Requirements
Must have
• Colors that are associated in the logo
Nice to have
• Sleek modern clean and chic design.

```html
<!DOCTYPE html>
<html lang="en">
<head>
<meta charset="utf-8">
<title>Harbor Crestline — Business Card</title>
<link rel="stylesheet" href="https://fonts.googleapis.com/css2?family=Montserrat:wght@600;700&family=Open+Sans:wght@400;600&display=swap">
<style>
  :root {
    --navy: #0c1744;
    --navy-deep: #08103a;
    --gold: #d4a83c;
    --white: #ffffff;
    --backdrop: #2b2b2d;
  }
  * { margin: 0; padding: 0; box-sizing: border-box; }
  html, body { width: 1200px; height: 780px; overflow: hidden; }
  body {
    background: var(--backdrop);
    position: relative;
    font-family: "Open Sans", Arial, sans-serif;
  }
  .card {
    position: absolute;
    top: 240px;
    width: 520px;
    height: 300px;
    border-radius: 24px;
    background: var(--navy);
    overflow: hidden;
  }
  .card--front { left: 50px; }
  .card--back { left: 630px; }

  .wordmark {
    display: flex;
    align-items: center;
    gap: 10px;
    font-family: "Montserrat", Arial, sans-serif;
    font-weight: 600;
    color: var(--white);
    text-transform: uppercase;
    letter-spacing: 0.14em;
    white-space: nowrap;
  }
  .wordmark__square {
    background: var(--gold);
    flex: none;
  }
  .card--front .wordmark {
    position: absolute;
    left: 36px;
    top: 34px;
    font-size: 19px;
  }
  .card--front .wordmark__square { width: 12px; height: 12px; }
  .card--back .wordmark {
    position: absolute;
    left: 50%;
    top: 50%;
    transform: translate(-50%, -50%);
    font-size: 28px;
  }
  .card--back .wordmark__square { width: 16px; height: 16px; }

  .address {
    position: absolute;
    left: 36px;
    top: 84px;
    color: var(--white);
    font-size: 13px;
    line-height: 1.45;
  }
  .contact-list {
    position: absolute;
    left: 36px;
    top: 136px;
    list-style: none;
    color: var(--white);
    font-size: 12.5px;
    line-height: 1.6;
  }
  .contact-list li { display: flex; align-items: center; gap: 8px; white-space: nowrap; }
  .contact-list svg { width: 12px; height: 12px; flex: none; }

  .person {
    position: absolute;
    right: 72px;
    top: 212px;
    text-align: right;
    white-space: nowrap;
  }
  .person__name {
    font-family: "Montserrat", Arial, sans-serif;
    font-weight: 700;
    font-size: 26px;
    line-height: 1.2;
    color: var(--gold);
    letter-spacing: 0.01em;
  }
  .person__title {
    font-size: 13px;
    color: var(--white);
    margin-top: 2px;
  }
  .corner-steps {
    position: absolute;
    right: 0;
    bottom: 0;
    width: 60px;
    height: 110px;
  }
</style>
</head>
<body>

  <section class="card card--front" aria-label="Front of business card">
    <div class="wordmark"><span class="wordmark__square"></span>Harbor Crestline</div>

    <p class="address">4120 Larkspur Ave<br>Suite 210, Brookhaven, OR 97301</p>

    <ul class="contact-list">
      <li>
        <svg viewBox="0 0 24 24" fill="var(--gold)"><path d="M6.6 10.8a15 15 0 0 0 6.6 6.6l2.2-2.2c.3-.3.7-.4 1-.2 1.1.4 2.3.6 3.6.6.6 0 1 .4 1 1V20c0 .6-.4 1-1 1A17 17 0 0 1 3 4c0-.6.4-1 1-1h3.5c.6 0 1 .4 1 1 0 1.3.2 2.5.6 3.6.1.3 0 .7-.2 1z"/></svg>
        (833) HarbCre / (833) 427-2731
      </li>
      <li>
        <svg viewBox="0 0 24 24" fill="none" stroke="var(--gold)" stroke-width="2.4"><circle cx="12" cy="12" r="9"/><path d="M3 12h18M12 3c3 3 3 15 0 18M12 3c-3 3-3 15 0 18"/></svg>
        www.theharborcrestline.com
      </li>
      <li>
        <svg viewBox="0 0 24 24" fill="none" stroke="var(--gold)" stroke-width="2.4"><rect x="3" y="5" width="18" height="14" rx="1"/><path d="M3 6l9 7 9-7"/></svg>
        dorian@theharborcrestline.com
      </li>
    </ul>

    <div class="person">
      <p class="person__name">Dorian Fenwick</p>
      <p class="person__title">CEO/Founder</p>
    </div>

    <svg class="corner-steps" viewBox="0 0 60 110" aria-hidden="true">
      <polygon points="60,0 60,110 22,110 22,88 30,88 30,66 38,66 38,44 46,44 46,22 54,22 54,0" fill="var(--gold)"/>
    </svg>
  </section>

  <section class="card card--back" aria-label="Back of business card">
    <div class="wordmark"><span class="wordmark__square"></span>Harbor Crestline</div>
  </section>

</body>
</html>
```